Cat-products company needs smart, yet endearing, business card

We need a business card design for a new, but up-and-running, business based in Honolulu, Hawaii. The business is Purrnest Nook Co. Our first product is the most environmentally-friendly cat grass kit ever seen on the planet. Future products, currently in the R&D phase, will include a variety of exciting cat scratchers. We also do consulting work to help apartment-dwellers make their home more cat-friendly and, in the future, plan on doing full, custom installs of structure to create high walkways for cats.

Target Market(s)

Middle-aged, apartment-dwelling, middle-class workers who own 1 or more cats and who dote on them.

Industry/Entity Type

Pet Care

Contact Information for Business Card

A striking, professional, yet warm and friendly design is what we're after.

Font styles to use
Serif
Sans Serif
Other font styles liked:
• Comfortaa

Colors

Designer to choose colors to be used in the design.

Requirements
Must have
• The company logo: (see attachment)
• The company name: Purrnest Nook Co
• The web address: www.purrnestnookco.com
• Email: support@purrnestnookco.com
• Phone: +1 (808) 571 6023
• Update (Fri Jun 30 3017 7:45pm Hawaii Time) I would like, is possible, uploaded picture of the cat grass kit on the back of the card with some text along the lines of: Purrnest Nook Co - Maker Of The Leafiest Feline Sprout Set Yet
Nice to have
• A cat picture, cartoon, real or silhouette that illustrates cats in action and/or relaxing; ie using the apartment space to live, play and relax in and being well-contented.
• Most of the website is done in the font: Comfortaa. It might be nice to continue using this for brand consistency.
Should not have
• Hard-to-read fonts.

```html
<!DOCTYPE html>
<html lang="en">
<head>
<meta charset="utf-8">
<title>Purrnest Nook Co – Business Card</title>
<link rel="stylesheet" href="https://fonts.googleapis.com/css2?family=Source+Sans+3:wght@400;600;700&display=swap">
<style>
  :root {
    --stage: #141414;
    --card-front: #ffffff;
    --card-back: #5b3630;
    --amber: #f9b200;
    --ink: #1e1e1e;
    --rule: #5b3630;
  }
  * { box-sizing: border-box; margin: 0; padding: 0; }
  html, body {
    width: 1200px; height: 900px; overflow: hidden;
    background: var(--stage);
    font-family: "Source Sans 3", "Myriad Pro", sans-serif;
  }
  .stage { position: relative; width: 1200px; height: 900px; }
  .card {
    position: absolute; top: 306px;
    width: 440px; height: 271px; border-radius: 11px;
  }
  .card--front { left: 149px; background: var(--card-front); }
  .card--back { left: 608px; background: var(--card-back);
    display: flex; align-items: center; justify-content: center; }

  .brand-lockup {
    position: absolute; left: 44px; top: 92px; width: 140px;
    text-align: center; color: var(--amber);
    font-weight: 700; font-size: 30px; line-height: 1.02;
  }
  .divider {
    position: absolute; left: 210px; top: 73px;
    width: 1px; height: 123px; background: var(--rule);
  }
  .person { position: absolute; left: 237px; top: 69px; }
  .person__name {
    color: var(--amber); font-size: 16.5px; font-weight: 400;
    letter-spacing: 0.2px; line-height: 1.1;
  }
  .person__title { color: var(--ink); font-size: 12.5px; line-height: 1.3; }

  .contact-list { position: absolute; left: 237px; top: 153px; list-style: none; }
  .contact-list li {
    display: flex; align-items: center; gap: 5px;
    color: var(--ink); font-size: 12.5px; line-height: 16px;
  }
  .contact-list svg { width: 10px; height: 10px; fill: var(--amber); flex: none; }

  .back-mark {
    color: var(--amber); font-weight: 700; font-size: 38px;
    text-align: center; line-height: 1.05;
  }
</style>
</head>
<body>
<main class="stage">
  <section class="card card--front" aria-label="Business card front">
    <div class="brand-lockup">Purrnest<br>Nook Co</div>
    <div class="divider"></div>
    <div class="person">
      <p class="person__name">MARCUS ELLERY</p>
      <p class="person__title">Managing Director</p>
    </div>
    <ul class="contact-list">
      <li>
        <svg viewBox="0 0 10 10" aria-hidden="true"><path d="M2 0.5 3.6 2.6 2.7 3.7C3.3 5 4.9 6.6 6.3 7.3L7.4 6.4 9.5 8 8.4 9.5C4.5 9.5 0.5 5.5 0.5 1.6Z"/></svg>
        +1 (808) 571 6023
      </li>
      <li>
        <svg viewBox="0 0 10 10" aria-hidden="true"><path d="M0.5 2H9.5V8.5H0.5Z M0.5 2 5 5.5 9.5 2" fill="var(--amber)"/><path d="M0.8 2.3 5 5.4 9.2 2.3" stroke="#fff" stroke-width="0.8" fill="none"/></svg>
        support@purrnestnookco.com
      </li>
      <li>
        <svg viewBox="0 0 10 10" aria-hidden="true"><circle cx="5" cy="5" r="4.5"/><path d="M3 3.5C4 3 4.5 4 5.5 4 6 5 5 6 4 6.5L3.5 8M6.5 6.5 7.5 7.5" stroke="#fff" stroke-width="0.8" fill="none"/></svg>
        www.purrnestnookco.com
      </li>
    </ul>
  </section>

  <section class="card card--back" aria-label="Business card back">
    <p class="back-mark">Purrnest<br>Nook Co</p>
  </section>
</main>
</body>
</html>
```